Consulting company business cards

We have a base design, but would be willing to update. We have a new logo/"tag" that needs to be added. Current business card design is attached for reference into our "style."

Industry/Entity Type

Business

Contact Information for Business Card

Should contain name and title, office number, mobile number if appropriate, e-mail, website, physical address, and company logo.

Font styles to use
Other font styles liked:
• See current card design on KorvandBCard

Colors
0455a3
85acd3
aaaaaa

Requirements
Must have
• Our colors are navy blue, gray, and a lighter blue
Nice to have
• Design that I can easily drop in new names/titles as we hire employees.

```html
<!DOCTYPE html>
<html lang="en">
<head>
<meta charset="utf-8">
<title>Brenwick Business Cards</title>
<link rel="stylesheet" href="https://fonts.googleapis.com/css2?family=Source+Sans+3:wght@400;600&display=swap">
<style>
  :root {
    --navy: #003350;
    --light-blue: #7fb0d3;
    --gray: #8a8a8a;
    --white: #ffffff;
    --stage: #dcdcdc;
  }
  * { box-sizing: border-box; margin: 0; padding: 0; }
  html, body {
    width: 1200px; height: 750px; overflow: hidden;
    background: var(--stage);
    font-family: "Source Sans 3", sans-serif;
  }
  .card {
    position: absolute; top: 228px;
    width: 461px; height: 262px;
    border-radius: 10px; overflow: hidden;
  }
  .card--front { left: 124px; background: var(--white); }
  .card--back { left: 618px; background: var(--navy); }

  .front-band { position: absolute; inset: 0; }

  .brand {
    position: absolute; left: 0; right: 0; top: 40px;
    display: flex; flex-direction: column; align-items: center;
  }
  .brand-row { display: flex; align-items: center; gap: 8px; }
  .brand-name {
    font-weight: 600; font-size: 44px; line-height: 1;
    color: var(--navy); letter-spacing: 0.04em;
  }
  .brand-dot {
    width: 34px; height: 34px; border-radius: 50%;
    background: var(--light-blue);
  }
  .brand-tagline {
    margin-top: 6px; font-size: 10px; letter-spacing: 0.16em;
    color: var(--gray);
  }

  .contact {
    position: absolute; left: 0; right: 0; top: 143px;
    text-align: center; color: var(--white);
  }
  .contact-name { font-weight: 600; font-size: 18px; line-height: 22px; }
  .contact-title { font-size: 14px; line-height: 16px; }
  .contact-lines { margin-top: 10px; font-size: 13px; line-height: 18px; }
  .contact-line { display: flex; justify-content: center; align-items: center; gap: 4px; }
  .contact-line .gap { width: 6px; }
  .icon { width: 12px; height: 12px; fill: var(--white); }
  .contact-address { margin-top: 4px; font-size: 13px; }

  .back-brand {
    position: absolute; left: 0; right: 0; top: 92px;
    display: flex; justify-content: center; align-items: center; gap: 10px;
  }
  .back-brand .brand-name { color: var(--white); font-size: 40px; }
  .back-brand .brand-dot { background: var(--white); width: 30px; height: 30px; }
  .back-web {
    position: absolute; left: 0; right: 0; top: 212px;
    text-align: center; color: var(--white);
    font-size: 13px; letter-spacing: 0.38em;
  }
</style>
</head>
<body>
  <section class="card card--front">
    <svg class="front-band" viewBox="0 0 461 262" width="461" height="262">
      <path d="M0,152 C22,138 52,132 92,132 L388,132 C420,132 446,142 461,160 L461,262 L0,262 Z" fill="var(--navy)"/>
    </svg>
    <div class="brand">
      <div class="brand-row">
        <span class="brand-name">BRENWICK</span>
        <span class="brand-dot"></span>
      </div>
      <div class="brand-tagline">A CLOUD CONSULTING COMPANY</div>
    </div>
    <div class="contact">
      <div class="contact-name">Tessakorvand</div>
      <div class="contact-title">Office Manager</div>
      <div class="contact-lines">
        <div class="contact-line">
          <svg class="icon" viewBox="0 0 12 12"><path d="M2.5 0.5 L4.5 0.5 L5 3.2 L3.7 4.2 C4.4 5.8 6 7.5 7.8 8.3 L8.8 7 L11.5 7.5 L11.5 9.6 C11.5 10.7 10.6 11.5 9.6 11.4 C4.8 11 1 7.2 0.6 2.4 C0.5 1.4 1.3 0.5 2.5 0.5 Z"/></svg>
          <span>555.014.3826</span>
          <svg class="icon" viewBox="0 0 12 12"><rect x="3" y="0.5" width="6" height="3"/><rect x="0.5" y="4" width="11" height="6" rx="1"/><rect x="2.5" y="10" width="7" height="1.5"/></svg>
          <span>555.014.3857</span>
        </div>
        <div class="contact-line">
          <svg class="icon" viewBox="0 0 12 12"><path d="M0.5 2.5 H11.5 V10 H0.5 Z M0.5 2.5 L6 7 L11.5 2.5" fill="none" stroke="var(--white)" stroke-width="1.2"/></svg>
          <span>tkorvand@brenwicktech.com</span>
          <span class="gap"></span>
          <svg class="icon" viewBox="0 0 12 12"><circle cx="6" cy="6" r="5.3" fill="none" stroke="var(--white)" stroke-width="1.2"/><path d="M1 6 H11 M6 0.7 C3.5 3.5 3.5 8.5 6 11.3 M6 0.7 C8.5 3.5 8.5 8.5 6 11.3" fill="none" stroke="var(--white)" stroke-width="0.9"/></svg>
          <span>www.brenwicktech.com</span>
        </div>
      </div>
      <div class="contact-address">1870 W 48th ST, Lakemont Ohio 40512</div>
    </div>
  </section>

  <section class="card card--back">
    <div class="back-brand">
      <span class="brand-name">BRENWICK</span>
      <span class="brand-dot"></span>
    </div>
    <div class="back-web">www.brenwicktech.com</div>
  </section>
</body>
</html>
```